Presentation Of Our Epidemiology Consulting Framework

We need a slide deck (png files) for PowerPoint that describes our organization and type of clients we serve, and our 6 phase framework that explains how we work with clients. Please use the minimum amount of text on each slide.  We want a more visual display of how to work with us. We want it to look very similar to our brochure.  We want to also have a few extra branded slides without text that can be used as a template if we decide to add to the deck later or create a new slide deck.
Colors
#56588C
#F28444
#F2E088
#F24C27
#ODODOD

```html
<!DOCTYPE html>
<html lang="en">
<head>
<meta charset="utf-8">
<title>Epidemiology Consulting Framework Deck</title>
<link rel="stylesheet" href="https://fonts.googleapis.com/css2?family=Lato:ital,wght@0,400;0,700;1,400&display=swap">
<style>
:root{
  --navy-top:#121130;
  --navy-bottom:#4a4781;
  --violet:#56588C;
  --orange:#F28444;
  --orange-deep:#F24C27;
  --white:#ffffff;
  --ink:#0D0D0D;
  --row:#4b4a80;
}
*{box-sizing:border-box;margin:0;padding:0}
html,body{width:1050px;height:1200px;overflow:hidden;background:#fff}
body{position:relative;font-family:"Lato",sans-serif;color:var(--white)}
.slide{position:absolute;width:454px;height:255px;overflow:hidden;
  background:linear-gradient(180deg,var(--navy-top) 0%,#2b2959 50%,var(--navy-bottom) 100%)}
.col-a{left:51px}.col-b{left:547px}
.row-1{top:41px}.row-2{top:329px}.row-3{top:617px}.row-4{top:905px}
.footer{position:absolute;left:0;top:230px;width:100%;height:17px;
  background:linear-gradient(90deg,var(--orange-deep),var(--orange));
  font-size:5.6px;line-height:17px;text-align:center;padding-right:60px}
.page-badge{position:absolute;top:229px;left:405px;width:20px;height:20px}
.page-badge span{position:absolute;inset:0;font-size:8px;font-weight:700;font-style:italic;
  text-align:center;line-height:20px}
.accent{color:var(--orange)}
.center{position:absolute;left:0;width:100%;text-align:center}
.brand{font-size:26px;font-weight:700;color:var(--orange);letter-spacing:.5px}
.brand .dot{display:inline-block;width:16px;height:16px;border-radius:50%;
  background:var(--orange);vertical-align:-1px;margin-right:8px}
.headline{font-size:22px;font-weight:700;line-height:26px}
.lede{font-size:9px;font-style:italic;line-height:13px}
.photo{position:absolute}
/* why partner */
.why-grid{position:absolute;left:175px;top:73px;width:270px;display:grid;
  grid-template-columns:1fr 1fr;row-gap:12px;column-gap:12px;text-align:center}
.why-grid h3{font-size:10.5px;color:var(--orange);font-weight:700;margin-bottom:4px}
.why-grid p{font-size:6.6px;line-height:10px}
/* discovery */
.steps{position:absolute;left:10px;top:123px;width:434px;display:flex}
.steps .step{flex:1;text-align:center;font-size:6.8px;line-height:10px;padding:0 6px}
.steps svg{display:block;margin:0 auto 6px;width:28px;height:28px}
/* launch */
.launch-title{position:absolute;left:22px;top:26px;font-size:22px;font-weight:700}
.launch-sub{position:absolute;left:23px;top:62px;font-size:8.8px;font-weight:700;color:var(--orange)}
.bullets{position:absolute;left:23px;top:86px;list-style:none}
.bullets li{font-size:9.2px;height:26px;display:flex;align-items:flex-start;gap:7px}
.bullets li::before{content:"";width:9px;height:9px;border-radius:50%;background:var(--orange);flex:none;margin-top:1px}
/* execution */
.exec-title{position:absolute;left:38px;top:54px;font-size:21px;font-weight:700;line-height:26px}
.exec-tag{position:absolute;left:38px;top:113px;font-size:9px;color:var(--orange);line-height:12px}
.exec-copy{position:absolute;left:38px;top:145px;font-size:9px;line-height:12px;width:115px}
.exec-row{position:absolute;left:199px;width:255px;height:35px;background:var(--row);
  font-size:9px;line-height:11.5px;display:flex;align-items:center;padding-left:56px;padding-right:12px}
.exec-row .badge{position:absolute;left:0;top:0;width:35px;height:35px;border-radius:50%;
  background:var(--orange);display:flex;align-items:center;justify-content:center}
/* evolution */
.evo-panel{position:absolute;left:52px;top:23px;width:350px;height:106px;border-radius:3px;
  background:linear-gradient(135deg,#4c4a82,#3b3970 60%,#4c4a84)}
.evo-items{position:absolute;left:20px;top:166px;width:420px;display:flex}
.evo-items div{flex:1;text-align:center;font-size:9.2px;line-height:11.5px}
.evo-items div::before{content:"";display:block;width:9px;height:9px;border-radius:50%;
  background:var(--orange);margin:0 auto 8px}
</style>
</head>
<body>

<!-- 01 title -->
<section class="slide col-a row-1">
  <div class="center brand" style="top:51px"><span class="dot"></span>Dr RLVance</div>
  <div class="center headline" style="top:102px">Transforming <span class="accent">Health Data</span> into<br>Community Impact</div>
  <div class="center lede" style="top:164px">At DrRLVance LLC, we bridge the gap between health data<br>and meaningful change.</div>
  <div class="footer">Copyright © 2025 Dr RLVance. All rights reserved.</div>
  <svg class="page-badge" viewBox="0 0 20 20"><rect x="4" y="4" width="12" height="12" rx="2" transform="rotate(45 10 10)" fill="#56588C" stroke="#fff" stroke-width=".8"/></svg>
  <div class="page-badge"><span>01</span></div>
</section>

<!-- 05 expert execution -->
<section class="slide col-b row-1">
  <div class="exec-title">Expert<br><span class="accent">Execution</span></div>
  <div class="exec-tag">Where Science Meets<br>Service</div>
  <div class="exec-copy">Our specialized team begins the transformation process:</div>
  <div class="exec-row" style="top:25px"><span class="badge"><svg width="18" height="18" viewBox="0 0 18 18" fill="none" stroke="#fff" stroke-width="1.3"><circle cx="8" cy="8" r="5"/><path d="M12 12l4 4"/></svg></span>In-depth research and analysis</div>
  <div class="exec-row" style="top:74px"><span class="badge"><svg width="18" height="18" viewBox="0 0 18 18" fill="none" stroke="#fff" stroke-width="1.3"><rect x="3" y="2" width="11" height="14" rx="1"/><path d="M6 6h5M6 9h5M6 12h3"/></svg></span>Content development and refinement</div>
  <div class="exec-row" style="top:123px"><span class="badge"><svg width="18" height="18" viewBox="0 0 18 18" fill="none" stroke="#fff" stroke-width="1.3"><path d="M2 16h14"/><rect x="4" y="9" width="2.5" height="6"/><rect x="8" y="6" width="2.5" height="9"/><rect x="12" y="3" width="2.5" height="12"/></svg></span>Data interpretation and visualization</div>
  <div class="exec-row" style="top:172px"><span class="badge"><svg width="18" height="18" viewBox="0 0 18 18" fill="none" stroke="#fff" stroke-width="1.3"><rect x="2" y="4" width="10" height="12" rx="1"/><path d="M6 2h10v11M5 8h4M5 11h4"/></svg></span>Plain language translation of complex health information</div>
  <div class="footer">Copyright © 2025 Dr RLVance. All rights reserved.</div>
  <svg class="page-badge" viewBox="0 0 20 20"><rect x="4" y="4" width="12" height="12" rx="2" transform="rotate(45 10 10)" fill="#56588C" stroke="#fff" stroke-width=".8"/></svg>
  <div class="page-badge"><span>05</span></div>
</section>

<!-- 02 why partner -->
<section class="slide col-a row-2" style="left:50px">
  <div class="photo" role="img" aria-label="Portrait photo of the founder in a dark blazer"
       style="left:0;top:22px;width:158px;height:233px;background:linear-gradient(180deg,#3a3348,#241f2e 60%,#1a1822)"></div>
  <div class="headline" style="position:absolute;left:178px;top:25px;width:260px;text-align:center">Why <span class="accent">Partner</span> With Us?</div>
  <div class="why-grid">
    <div><h3>Impact</h3><p>Proven track record of<br>transforming complex health<br>data into accessible<br>information</p></div>
    <div><h3>Innovation</h3><p>Custom solutions tailored to<br>BIPOC community needs</p></div>
    <div><h3>Expertise</h3><p>Our diverse team of innovative<br>global public health professionals,<br>specialized in epidemiology and<br>health communication</p></div>
    <div><h3>Partnership</h3><p>Collaborative approach<br>ensuring lasting results</p></div>
  </div>
  <div class="footer">Copyright © 2025 Dr RLVance. All rights reserved.</div>
  <svg class="page-badge" viewBox="0 0 20 20"><rect x="4" y="4" width="12" height="12" rx="2" transform="rotate(45 10 10)" fill="#56588C" stroke="#fff" stroke-width=".8"/></svg>
  <div class="page-badge"><span>02</span></div>
</section>

<!-- 06 master -->
<section class="slide col-b row-2">
  <div class="center headline" style="top:98px">Master <span class="accent">Slide</span></div>
  <div class="footer">Copyright © 2025 Dr RLVance. All rights reserved.</div>
  <svg class="page-badge" viewBox="0 0 20 20"><rect x="4" y="4" width="12" height="12" rx="2" transform="rotate(45 10 10)" fill="#56588C" stroke="#fff" stroke-width=".8"/></svg>
  <div class="page-badge"><span>06</span></div>
</section>

<!-- 03 discovery -->
<section class="slide col-a row-3">
  <div class="center headline" style="top:56px">Discovery &amp; <span class="accent">Vision Alignment</span></div>
  <div class="center" style="top:93px;font-size:9px;font-weight:700;color:var(--orange)">Building the Foundation for Success</div>
  <div class="steps">
    <div class="step"><svg viewBox="0 0 28 28" fill="none" stroke="#F24C27" stroke-width="1.3"><circle cx="14" cy="14" r="11" stroke-dasharray="4 2"/><circle cx="14" cy="14" r="7"/><circle cx="11" cy="13" r="1.5"/><circle cx="17" cy="13" r="1.5"/></svg>Deep-dive exploration of your organization's unique challenges and opportunities</div>
    <div class="step"><svg viewBox="0 0 28 28" fill="none" stroke="#F24C27" stroke-width="1.3"><circle cx="14" cy="14" r="12"/><circle cx="14" cy="14" r="8"/><circle cx="14" cy="14" r="4"/><path d="M14 14l9-9M20 5h3v3"/></svg>Strategic alignment of goals and expectations</div>
    <div class="step"><svg viewBox="0 0 28 28" fill="none" stroke="#F24C27" stroke-width="1.3"><rect x="3" y="2" width="6" height="8"/><rect x="11" y="2" width="6" height="8"/><rect x="19" y="2" width="6" height="8"/><path d="M14 10v6M6 10v3h16v-3M4 22h6l6 3 8-5"/></svg>Custom-tailored solution design</div>
    <div class="step"><svg viewBox="0 0 28 28" fill="none" stroke="#F24C27" stroke-width="1.3"><rect x="2" y="4" width="20" height="16" rx="2"/><path d="M2 9h20M9 13l-2 2 2 2M15 13l2 2-2 2"/><circle cx="22" cy="21" r="4"/></svg>Clear roadmap development with defined milestones</div>
  </div>
  <div class="footer">Copyright © 2025 Dr RLVance. All rights reserved.</div>
  <svg class="page-badge" viewBox="0 0 20 20"><rect x="4" y="4" width="12" height="12" rx="2" transform="rotate(45 10 10)" fill="#56588C" stroke="#fff" stroke-width=".8"/></svg>
  <div class="page-badge"><span>03</span></div>
</section>

<!-- 07 evolution -->
<section class="slide col-b row-3">
  <div class="evo-panel" role="img" aria-label="Faint background photo of a business meeting"></div>
  <div class="center headline" style="top:51px">Evolution &amp; <span class="accent">Growth</span></div>
  <div class="center" style="top:87px;font-size:9px;font-weight:700;color:var(--orange)">Sustaining Long-term Success</div>
  <div class="evo-items">
    <div>Project success<br>celebration</div>
    <div>Future opportunities<br>exploration</div>
    <div>Partnership<br>evolution planning</div>
    <div>Continuous improvement<br>recommendations</div>
  </div>
  <div class="footer">Copyright © 2025 Dr RLVance. All rights reserved.</div>
  <svg class="page-badge" viewBox="0 0 20 20"><rect x="4" y="4" width="12" height="12" rx="2" transform="rotate(45 10 10)" fill="#56588C" stroke="#fff" stroke-width=".8"/></svg>
  <div class="page-badge"><span>07</span></div>
</section>

<!-- 04 launch -->
<section class="slide col-a row-4">
  <div class="launch-title">Partnership <span class="accent">Launch</span></div>
  <div class="launch-sub">Setting the Stage for Excellence</div>
  <ul class="bullets">
    <li>Formation of dedicated project team</li>
    <li>Establishment of collaborative workflow</li>
    <li>Comprehensive data gathering</li>
    <li>Strategic timeline planning</li>
    <li>Stakeholder engagement and vision capture</li>
  </ul>
  <div class="photo" role="img" aria-label="Photo of two colleagues reviewing a tablet together"
       style="left:250px;top:25px;width:181px;height:180px;border:1.5px solid var(--orange);background:linear-gradient(160deg,#6f7f90,#3f5878 55%,#2a3142)"></div>
  <div class="footer">Copyright © 2025 Dr RLVance. All rights reserved.</div>
  <svg class="page-badge" viewBox="0 0 20 20"><rect x="4" y="4" width="12" height="12" rx="2" transform="rotate(45 10 10)" fill="#56588C" stroke="#fff" stroke-width=".8"/></svg>
  <div class="page-badge"><span>04</span></div>
</section>

<!-- 08 thank you -->
<section class="slide col-b row-4">
  <div class="center brand" style="top:52px"><span class="dot"></span>Dr RLVance</div>
  <div class="center headline" style="top:104px">Thank You for <span class="accent">Your Partnership</span><br>and Trust</div>
  <div class="center lede" style="top:168px">We appreciate your commitment to transforming health data into<br>impactful change for BIPOC communities.</div>
  <div class="footer">Copyright © 2025 Dr RLVance. All rights reserved.</div>
  <svg class="page-badge" viewBox="0 0 20 20"><rect x="4" y="4" width="12" height="12" rx="2" transform="rotate(45 10 10)" fill="#56588C" stroke="#fff" stroke-width=".8"/></svg>
  <div class="page-badge"><span>08</span></div>
</section>

</body>
</html>
```